Studio Ombre Bleue (Masterclasses for Actors) needs artistic and modern website in French & English

Hello!

We need to create a new website (existing : www.lune-rouge-studio.example) for our acting school that holds Masterclasses for professional actors in Paris. It needs to be in French and English with an easy to use back office (wordpress is slow and complicated) (ideas?) so we can add or change workshop dates, upload new photos or videos to the gallery ourselves and make basic changes to the information on line.

Our main clients are French but we have international guests coming who only understand english.

Ideally you would know how to link your creation to the existing domain name, how to make sure the email adresses remain the same and help us find the least expensive but best all in 1 proposition to make it as easy as possible to pay the yearly fee to the hosting platform / web name / etc :-)

Design wise we would like something creative, linked to films etc but without using to many clichés. The logo and a stamp have already been created and we would like to keep these (which has the colours we would like you to use).

It would be nice to maybe have a moving image when you first open the page, maybe the logo itself, something dynamic and visual...

Thank you for you time in reading this!

Margot & Ninon & Apolline
Team LRS

Target Market(s)

actors

Coding

Coded - Design and coding required

Number of Pages Required

5+ page

Font styles to use
Sans Serif

Colors
34a7d8

Requirements
Must have
• able to be read on all electronic devices
Nice to have
• some fun and humour / class
Should not have
• too corporate

```html
<!DOCTYPE html>
<html lang="fr">
<head>
<meta charset="utf-8">
<title>Studio Ombre Bleue — Masterclasses pour comédiens</title>
<link href="https://fonts.googleapis.com/css2?family=Lato:ital,wght@0,400;0,700;0,900;1,400&family=Open+Sans:ital,wght@0,400;0,600;1,400&family=Oswald:wght@400;500&display=swap" rel="stylesheet">
<style>
:root{
  --blue:#318ed4;
  --ink:#1d1d1d;
  --text:#444;
  --muted:#888;
  --paper:#f5f5f5;
  --white:#fff;
  --map:#eceef0;
}
*{margin:0;padding:0;box-sizing:border-box}
html,body{width:1200px;height:2812px;overflow:hidden}
body{position:relative;background:var(--white);font-family:"Open Sans",Arial,sans-serif;color:var(--text)}
.abs{position:absolute}

/* hero */
.hero{left:0;top:0;width:1200px;height:705px;background:radial-gradient(ellipse at 45% 45%,#4a4540 0%,#2b2825 50%,#151414 100%)}
.brand{left:98px;top:48px;display:flex;align-items:center;gap:12px}
.brand-dot{width:22px;height:22px;border-radius:50%;background:var(--blue)}
.brand-name{font-family:"Lato",sans-serif;font-weight:400;font-size:30px;color:var(--white);letter-spacing:1px}
.lang{left:970px;top:0;width:132px;height:30px;background:var(--blue);color:var(--white);font-size:11px;font-family:"Lato",sans-serif;display:flex;align-items:center;justify-content:center;gap:10px}
.nav{left:506px;top:56px;display:flex;font-family:"Lato",sans-serif;font-size:12.5px;color:#ddd}
.nav a{color:inherit;text-decoration:none;padding:6px 9px;margin-right:6px}
.nav a.active{border:1px solid #ddd;color:var(--white)}
.hero-title{left:0;top:250px;width:1200px;text-align:center;font-family:"Oswald",sans-serif;font-weight:400;font-size:24px;line-height:38px;color:var(--white);text-transform:uppercase}
.hero-rule{left:529px;top:346px;width:144px;height:3px;background:var(--blue)}
.hero-lead{left:355px;top:372px;width:490px;text-align:center;font-size:16px;line-height:25px;color:#e6e6e6}
.hero-ctrl{left:552px;top:644px;display:flex;align-items:center;gap:16px}
.hero-ctrl .box{width:34px;height:34px;border:2px solid #aaa;display:flex;align-items:center;justify-content:center}

/* portfolio */
.portfolio{left:0;top:705px;width:1200px;height:900px;background:var(--paper)}
.sec-title{width:1200px;left:0;text-align:center;font-family:"Lato",sans-serif;font-weight:900;font-size:28px;color:var(--ink)}
.sec-sub{width:1200px;left:0;text-align:center;font-family:"Lato",sans-serif;font-size:21px;color:#333}
.filters{left:409px;top:886px;display:flex;gap:5px;font-family:"Lato",sans-serif;font-size:11px}
.filters span{height:28px;border:1px solid #ccc;background:var(--white);display:flex;align-items:center;padding:0 14px;color:#555}
.filters span.on{color:var(--blue);background:#eef2f5}
.card{width:257px;text-align:center;font-family:"Lato",sans-serif}
.card .thumb{height:139px;margin-bottom:24px}
.card h3{font-size:13.5px;font-weight:700;color:var(--ink);margin-bottom:6px}
.card p{font-size:11px;color:#333}
.t-dark{background:linear-gradient(135deg,#23282b,#0d1012)}
.t-group{background:linear-gradient(180deg,#bfb4a8,#4b4240)}
.t-crowd{background:linear-gradient(180deg,#d7d2cc,#5a5f66)}
.t-party{background:linear-gradient(180deg,#cfc8bd,#6a5a55)}
.t-park{background:linear-gradient(180deg,#cfd8d8 0%,#6e8a4c 55%,#3f6a23 100%)}
.t-house{background:linear-gradient(180deg,#c7d3dc 0%,#d9d2c8 45%,#4d6b2e 100%)}
.load{left:531px;top:1500px;width:120px;height:28px;background:var(--blue);color:var(--white);font-family:"Lato",sans-serif;font-size:11px;display:flex;align-items:center;justify-content:center}

/* testimonial */
.quote-band{left:0;top:1490px;width:1200px;height:720px}
.quote-text{left:262px;top:1854px;width:676px;text-align:center;font-style:italic;font-size:15px;line-height:20px;color:#eee}
.dots{left:560px;top:1974px;display:flex;gap:6px}
.dots i{width:9px;height:9px;border-radius:50%;background:#ddd;display:block}
.author{left:0;top:2006px;width:1200px;text-align:center;font-family:"Lato",sans-serif;font-size:18px;color:var(--white)}
.author small{font-size:14px;color:#aaa}

/* contact */
.contact{left:0;top:2110px;width:1200px;height:523px;background:linear-gradient(180deg,var(--map),#e4e7ea)}
.info-strip{left:99px;top:2316px;width:51px;height:230px;background:var(--blue)}
.info{left:176px;font-family:"Lato",sans-serif}
.info h4{font-size:12px;font-weight:700;color:#333;letter-spacing:.5px;margin-bottom:8px}
.info p{font-size:10.5px;line-height:19px;color:#555}
.form{left:442px;top:2316px;width:606px;height:230px;background:var(--white);font-family:"Lato",sans-serif;font-size:11px;color:#999}
.form .field{position:absolute;top:0;height:41px;border-bottom:1px solid #e3e3e3;padding:13px 8px}
.send{left:1050px;top:2316px;width:51px;height:230px;background:var(--blue);display:flex;align-items:center;justify-content:center}

/* footer */
.footer{left:0;top:2633px;width:1200px;height:127px;background:var(--blue)}
.social{top:2676px;width:43px;height:43px;border:2px solid var(--white);color:var(--white);font-family:"Lato",sans-serif;font-size:10px;display:flex;align-items:center;justify-content:center}
.legal{left:96px;top:2778px;font-family:"Lato",sans-serif;font-size:12px;color:#333}
.to-top{left:1073px;top:2771px;width:28px;height:28px}
</style>
</head>
<body>

<!-- HERO -->
<section class="abs hero" role="img" aria-label="Photo sombre d'un vieux projecteur de cinéma et d'un clap"></section>
<div class="abs brand"><span class="brand-dot"></span><span class="brand-name">Studio Ombre Bleue</span></div>
<div class="abs lang">Language: Eng
  <svg width="9" height="6" viewBox="0 0 9 6"><path d="M1 1l3.5 3.5L8 1" stroke="#fff" stroke-width="1.5" fill="none"/></svg>
</div>
<nav class="abs nav">
  <a class="active">A propos</a><a>Stages</a><a>Photos</a><a>Videos</a><a>Evenements</a><a>L'équipe</a><a>Partenaires</a><a>Blog</a>
</nav>
<h1 class="abs hero-title">We are an acting school that holds masterclasses<br>for professional actors in Paris</h1>
<div class="abs hero-rule"></div>
<p class="abs hero-lead">Pellentesque pharetra in dui vitae porta. Aliquam porttitor purus et sapien dapibus varius. Quisque bibendum vehicula consectetur. Donec</p>
<div class="abs hero-ctrl">
  <svg width="14" height="24" viewBox="0 0 14 24"><path d="M12 2L2 12l10 10" stroke="#aaa" stroke-width="2" fill="none"/></svg>
  <span class="box"><svg width="16" height="10" viewBox="0 0 16 10"><path d="M2 2l6 6 6-6" stroke="#4aa3e6" stroke-width="2.5" fill="none"/></svg></span>
  <svg width="14" height="24" viewBox="0 0 14 24"><path d="M2 2l10 10L2 22" stroke="#aaa" stroke-width="2" fill="none"/></svg>
</div>

<!-- PORTFOLIO -->
<section class="abs portfolio"></section>
<h2 class="abs sec-title" style="top:774px">PORTFOLIO</h2>
<p class="abs sec-sub" style="top:808px">Contrary to popular belief, Lorem Ipsum</p>
<div class="abs filters"><span class="on">ALL</span><span>STAGES</span><span>COACHING</span><span>SOIREE NETWORKING</span><span>LIEU</span></div>

<article class="abs card" style="left:191px;top:979px">
  <div class="thumb t-dark" role="img" aria-label="Photo d'un comédien sur un plateau sombre" style="position:relative">
    <svg style="position:absolute;left:105px;top:58px" width="50" height="20" viewBox="0 0 50 20"><circle cx="8" cy="8" r="6" stroke="#3aa0e8" stroke-width="2.5" fill="none"/><path d="M12 12l5 5" stroke="#3aa0e8" stroke-width="2.5"/><path d="M34 12l6-6M32 8a3 3 0 014 0M38 14a3 3 0 01-4 0" stroke="#ccc" stroke-width="1.8" fill="none"/></svg>
  </div>
  <h3>Outfield</h3><p>Contrary to popular belief, Lorem Ipsum</p>
</article>
<article class="abs card" style="left:465px;top:979px">
  <div class="thumb t-group" role="img" aria-label="Photo de groupe des participants d'un stage"></div>
  <h3>Amit Lorem</h3><p>Contrary to popular belief, Lorem Ipsum</p>
</article>
<article class="abs card" style="left:739px;top:979px">
  <div class="thumb t-crowd" role="img" aria-label="Photo de groupe d'une masterclass"></div>
  <h3>Contatntry Popilar</h3><p>Contrary to popular belief, Lorem Ipsum</p>
</article>
<article class="abs card" style="left:191px;top:1222px">
  <div class="thumb t-party" role="img" aria-label="Photo de groupe lors d'une soirée"></div>
  <h3>Dolor sit</h3><p>Contrary to popular belief, Lorem Ipsum</p>
</article>
<article class="abs card" style="left:465px;top:1222px">
  <div class="thumb t-park" role="img" aria-label="Photo d'une pelouse bordée d'arbres"></div>
  <h3>Outfield</h3><p>Contrary to popular belief, Lorem Ipsum</p>
</article>
<article class="abs card" style="left:739px;top:1222px">
  <div class="thumb t-house" role="img" aria-label="Photo d'une maison de campagne, lieu des stages"></div>
  <h3>Outfield</h3><p>Contrary to popular belief, Lorem Ipsum</p>
</article>
<div class="abs load">LOAD MORE</div>

<!-- TESTIMONIAL -->
<svg class="abs quote-band" viewBox="0 1490 1200 720" width="1200" height="720" role="img" aria-label="Photo sombre d'un intérieur avec une tasse, en fond de témoignage">
  <defs>
    <linearGradient id="darkFill" x1="0" y1="0" x2="0" y2="1">
      <stop offset="0" stop-color="#2b2724"/><stop offset=".5" stop-color="#3a332d"/><stop offset="1" stop-color="#1b1917"/>
    </linearGradient>
  </defs>
  <polygon points="0,1581 1200,1500 1200,2112 0,2200" fill="url(#darkFill)"/>
  <polygon points="680,2125 1200,2072 1200,2185" fill="#318ed4"/>
  <g fill="#318ed4">
    <rect x="549" y="1727" width="46" height="38"/>
    <path d="M572 1765h23c0 24-8 42-28 50l-4-10c10-8 12-20 9-40z"/>
    <rect x="605" y="1727" width="46" height="38"/>
    <path d="M628 1765h23c0 24-8 42-28 50l-4-10c10-8 12-20 9-40z"/>
  </g>
</svg>
<p class="abs quote-text">Lorem Ipsum is simply dummy text of the printing and typesetting industry. Lorem Ipsum has been the industry's standard dummy text ever since the 1500s, when an unknown printer took a galley of type and</p>
<div class="abs dots"><i></i><i></i><i></i><i></i></div>
<p class="abs author">Jhon Doe, <small>Lorem ipsum dolor</small></p>

<!-- CONTACT -->
<section class="abs contact" role="img" aria-label="Plan de ville en fond clair" style="z-index:-1"></section>
<h2 class="abs sec-title" style="top:2193px">CONTACT US</h2>
<p class="abs sec-sub" style="top:2228px">Contrary to popular belief, Lorem Ipsum</p>

<div class="abs info-strip">
  <svg width="51" height="230" viewBox="0 0 51 230" fill="#fff">
    <path d="M21 24h10l-2 8 4 4H19l4-4z M25 36v8" stroke="#fff" stroke-width="2"/>
    <rect x="19" y="110" width="14" height="16" rx="3" fill="none" stroke="#fff" stroke-width="2"/>
    <rect x="22" y="114" width="8" height="6"/>
    <rect x="17" y="196" width="18" height="13"/>
    <path d="M17 196l9 7 9-7" stroke="#318ed4" stroke-width="1.5" fill="none"/>
  </svg>
</div>
<div class="abs info" style="top:2322px"><h4>ADDRESS</h4><p>Quai des Lanternes, Paris<br>Rue 21</p></div>
<div class="abs info" style="top:2398px"><h4>PHONE</h4><p>+33 6 00 00 12 34</p></div>
<div class="abs info" style="top:2474px"><h4>MAIL</h4><p>contact@studio-ombre-bleue.example</p></div>

<div class="abs form">
  <div class="field" style="left:0;width:300px;border-right:1px solid #e3e3e3">Name*</div>
  <div class="field" style="left:300px;width:306px">Mail*</div>
  <div style="position:absolute;left:8px;top:54px">Type your message here ...</div>
</div>
<div class="abs send">
  <svg width="22" height="22" viewBox="0 0 22 22"><path d="M2 10L20 2l-6 18-3-7z" fill="#fff"/></svg>
</div>

<!-- FOOTER -->
<footer class="abs footer"></footer>
<div class="abs social" style="left:442px">Fil</div>
<div class="abs social" style="left:510px">Voix</div>
<div class="abs social" style="left:578px">Album</div>
<div class="abs social" style="left:647px">Cercle</div>
<div class="abs social" style="left:714px">Vidéo</div>
<p class="abs legal">2016 © Studio Ombre Bleue. All rights reserved.</p>
<svg class="abs to-top" viewBox="0 0 28 28"><circle cx="14" cy="14" r="12" stroke="#333" stroke-width="1.5" fill="none"/><path d="M14 20V8M9 13l5-5 5 5" stroke="#333" stroke-width="1.5" fill="none"/></svg>

</body>
</html>
```